Yacht, Boats, Watersports company needs a redesign of business card

Hello Designers!
We are a Boat dealership company that sells fun in the water, we sell boats, Yachts, Kayaks and also yacht WaterSport toys. We are looking to redesign our business cards in to something a little bit more sophisticated. in a way that we can make better use of our company colors. I'm attaching a zipped file containing the company 3 sets of company logo which one is an horizontal another one is a vertical and also a chromed 3d logo. Also is included two set of business cards that we use and also some designs that i think it's interesting. We use PMS 2026c Orange and PMS 7687C Blue. I would like to see at least two different options with the orange as accent and also using blue as an accent color. It's really important for the business cards to have a font option and size that is legible to most people. Our current website is wwww.coralpennant.com. Please visit if you want to have a better feeling of the Boat dealership
You can send Single sided or double side options. We are now using single sided but we may be open for a double side option if we really like the design.
Target Market(s)
Marine, boat sales, yacht sales, water toys sales/
Contact Information for Business Card
Name: Dale Whitcombe
Address: 212 North Fenwick Lane,
Harbor Cove, FL 33190
Phone: 954-731-8842
Fax: 954:731-8843
Cell: 954-382-1490
Email: dw@coralpennant.com
Website: coralpennant.com
Requirements
Must have
- the current information of the business card provided.
logo
use the PMS Colors
Nice to have
- a touch of elegance and sophistication but simple
Should not have
- should not have any typography that is hard to read, the card should be simple but yet sophisticated.

```html
<!DOCTYPE html>
<html lang="en">
<head>
<meta charset="utf-8">
<title>Coral Pennant – Business Card</title>
<link rel="stylesheet" href="https://fonts.googleapis.com/css2?family=Montserrat:wght@600;700&family=Work+Sans:wght@400;500&display=swap">
<style>
  :root {
    --brand-blue: #1b4a80;
    --brand-orange: #e2571f;
    --ink: #3a3d42;
    --card: #f3f4f5;
    --backdrop: #dcd6cd;
  }
  * { margin: 0; padding: 0; box-sizing: border-box; }
  html, body { width: 1200px; height: 887px; overflow: hidden; background: var(--backdrop); }
  .card {
    position: absolute; left: 80px; top: 158px; width: 1040px; height: 570px;
    background: var(--card); border-radius: 22px; overflow: hidden;
    box-shadow: 0 10px 30px rgba(0,0,0,0.12);
    font-family: "Work Sans", Arial, sans-serif; color: var(--ink);
  }
  .brand { position: absolute; left: 61px; top: 52px; display: flex; align-items: center; gap: 18px; }
  .brand-dot { width: 76px; height: 76px; border-radius: 50%; border: 7px solid var(--brand-orange); }
  .brand-name {
    font-family: "Montserrat", Arial, sans-serif; font-weight: 700; font-size: 20px;
    letter-spacing: 1px; text-transform: uppercase; color: var(--brand-blue);
  }
  .holder-name {
    position: absolute; left: 60px; top: 190px;
    font-family: "Montserrat", Arial, sans-serif; font-weight: 700; font-size: 38px;
    letter-spacing: 2px; text-transform: uppercase; color: var(--brand-blue);
  }
  .accent-dash { position: absolute; left: 61px; top: 249px; width: 22px; height: 3px; background: var(--brand-orange); }
  .address { position: absolute; left: 60px; top: 272px; font-size: 23px; line-height: 32px; letter-spacing: 0.6px; }
  .contacts { position: absolute; left: 60px; top: 350px; list-style: none; font-size: 23px; line-height: 32px; letter-spacing: 0.6px; }
  .contacts li { display: flex; align-items: center; gap: 8px; white-space: nowrap; }
  .contacts svg { width: 17px; height: 17px; fill: none; stroke: var(--brand-orange); stroke-width: 2; flex: none; }
  .contacts .site-name { font-weight: 500; color: var(--brand-blue); }
  .wordmark-large {
    position: absolute; left: 600px; top: 150px; width: 380px; text-align: center;
    font-family: "Montserrat", Arial, sans-serif; font-weight: 700; font-size: 62px; line-height: 1.15;
    letter-spacing: 3px; text-transform: uppercase; color: var(--brand-blue);
  }
  .rule-orange { position: absolute; left: 0; right: 0; top: 534px; height: 3px; background: var(--brand-orange); }
  .band-blue { position: absolute; left: 0; right: 0; top: 541px; bottom: 0; background: var(--brand-blue); }
</style>
</head>
<body>
<div class="card">
  <div class="brand">
    <div class="brand-dot"></div>
    <div class="brand-name">Coral Pennant</div>
  </div>

  <h1 class="holder-name">Dale Whitcombe</h1>
  <div class="accent-dash"></div>

  <p class="address">212 North Fenwick Lane,<br>Harbor Cove, FL 33190</p>

  <ul class="contacts">
    <li><svg viewBox="0 0 24 24"><path d="M5 3h4l2 5-3 2a12 12 0 0 0 6 6l2-3 5 2v4a2 2 0 0 1-2 2A18 18 0 0 1 3 5a2 2 0 0 1 2-2z"/></svg><span>954-731-8842</span></li>
    <li><svg viewBox="0 0 24 24"><rect x="6" y="3" width="12" height="6"/><rect x="3" y="9" width="18" height="8" rx="1"/><rect x="7" y="14" width="10" height="7"/></svg><span>954:731-8843</span></li>
    <li><svg viewBox="0 0 24 24"><rect x="7" y="2" width="10" height="20" rx="2"/><line x1="11" y1="18" x2="13" y2="18"/></svg><span>954-382-1490</span></li>
    <li><svg viewBox="0 0 24 24"><rect x="3" y="5" width="18" height="14" rx="1"/><path d="M3 6l9 7 9-7"/></svg><span>dw@coralpennant.com</span></li>
    <li><svg viewBox="0 0 24 24"><circle cx="12" cy="12" r="9"/><ellipse cx="12" cy="12" rx="4" ry="9"/><line x1="3" y1="12" x2="21" y2="12"/></svg><span>www.<span class="site-name">coralpennant</span>.com</span></li>
  </ul>

  <div class="wordmark-large">Coral<br>Pennant</div>

  <div class="rule-orange"></div>
  <div class="band-blue"></div>
</div>
</body>
</html>
```